Book for new dads needs a cover.

We need a cover for a book titled Roadmap to Early Parenthood: Practical Methods for Welcoming a Newborn, Juggling Career and Home Life, and Managing Mental Health on the Path to Becoming a Parent. We would like to see a design that emphasizes healthy babies and confident dads.

```html
<!DOCTYPE html>
<html lang="en">
<head>
<meta charset="utf-8">
<title>Roadmap to Early Parenthood – Book Cover</title>
<link rel="stylesheet" href="https://fonts.googleapis.com/css2?family=DM+Sans:wght@300;400;600;700&family=Montserrat:wght@500;600&display=swap">
<style>
  :root {
    --page-bg: #ffffff;
    --green-top: #72c68a;
    --green-mid: #7db58a;
    --green-bottom: #69aa76;
    --ink-purple: #35287a;
    --badge-purple: #5b46a3;
    --badge-edge: #8e7fd0;
    --band-purple: #54449a;
    --title-white: #ffffff;
    --title-shade: #d9dcdc;
    --art-orange: #f0974a;
    --art-violet: #6a57c4;
    --art-green: #8fd19a;
  }
  * { box-sizing: border-box; margin: 0; padding: 0; }
  html, body {
    width: 1200px; height: 1000px; overflow: hidden;
    background: var(--page-bg);
  }
  .canvas { position: relative; width: 1200px; height: 1000px; }
  .cover {
    position: absolute; left: 268px; top: 0;
    width: 665px; height: 1000px;
    background: linear-gradient(180deg, var(--green-top) 0%, var(--green-mid) 50%, var(--green-bottom) 100%);
    overflow: hidden;
    font-family: "DM Sans", sans-serif;
    text-align: center;
  }
  .subtitle { position: absolute; top: 24px; left: 0; right: 0; color: var(--ink-purple); }
  .subtitle-lead { font-weight: 700; font-size: 21px; letter-spacing: 0.6px; line-height: 26px; }
  .subtitle-rest { font-weight: 600; font-size: 16px; line-height: 22px; margin-top: 2px; padding: 0 60px; }
  .title { position: absolute; left: 0; right: 0; color: var(--title-white); font-weight: 300; line-height: 1; }
  .title-top { top: 118px; font-size: 104px; letter-spacing: 1px; }
  .title-badge {
    position: absolute; top: 208px; left: 50%;
    transform: translateX(-50%) rotate(-3deg);
    background: var(--badge-purple);
    border: 2px solid var(--badge-edge);
    color: var(--title-white);
    font-weight: 400; font-size: 56px; line-height: 1;
    padding: 3px 22px 5px;
  }
  .title-middle { top: 284px; font-size: 100px; }
  .title-bottom {
    top: 400px; font-size: 104px; font-weight: 400; letter-spacing: -1px;
    background: linear-gradient(180deg, var(--title-white) 40%, var(--title-shade) 100%);
    -webkit-background-clip: text; background-clip: text; color: transparent;
  }
  .illustration {
    position: absolute; left: 147px; top: 488px; width: 375px; height: 440px;
    border-radius: 160px 160px 0 0;
    background: radial-gradient(circle at 50% 45%, var(--art-green) 0%, var(--art-orange) 40%, var(--art-violet) 80%);
    opacity: 0.85;
  }
  .author-band {
    position: absolute; left: 0; bottom: 0; width: 100%; height: 72px;
    background: var(--band-purple);
    display: flex; align-items: center; justify-content: center;
  }
  .author-name {
    font-family: "Montserrat", sans-serif; font-weight: 500;
    color: var(--title-white); font-size: 34px; letter-spacing: 9px;
  }
</style>
</head>
<body>
<div class="canvas">
  <main class="cover">
    <header class="subtitle">
      <p class="subtitle-lead">PRACTICAL METHODS FOR WELCOMING</p>
      <p class="subtitle-rest">a Newborn, Juggling Career and Home Life, and Managing Mental Health on the Path to Becoming a Parent</p>
    </header>
    <h1>
      <span class="title title-top">ROADMAP</span>
      <span class="title-badge">TO</span>
      <span class="title title-middle">EARLY</span>
      <span class="title title-bottom">PARENTHOOD</span>
    </h1>
    <div class="illustration" role="img" aria-label="Illustration of a smiling couple holding their newborn baby together"></div>
    <footer class="author-band">
      <p class="author-name">MARION K. HALE</p>
    </footer>
  </main>
</div>
</body>
</html>
```